National Sales - Pick Up Truck Dealer

We need a logo design for a new vehicle dealership based in Sydney, Australia. The business name is Coastal Iron Haulers Motor Co. We will be selling American 'trucks/pick up trucks' like KRV, Torvan, Blaxer, Morrow T420, Kenzo Raptors, Morrow T640 and the likes.

These vehicles are a luxury option and we would like the logo to be strong, luxurious and masculine.Colours will be black and red or black and blue with the option of grey and white.

Target Market(s)

Men

Industry/Entity Type

Car Dealer

Contact Information for Business Card

Dennis Harlowe
Managing Director
0412 639 274
den@qelvtrk.com.au

Level 5, Brindle Parkway
17 Pemberly Lane
Baulkham Hills
NSW
Australia
Licence No: MD493152

Back of the card

qelvtrk.com.au

Font styles to use
Sans Serif

Colors

Designer to choose colors to be used in the design.

Requirements
Must have
• The company logo that is in the attachments, you can choose from the three which one you would like to work with. Must have vehicle images ....Please look at the attachments as they show examples of what we like and also provides potential images. If you choose to put an image on the front even if it is just the front of the vehicle can you please use the Black KRV Sorrento. Must have all details from the business card details section front and back
Nice to have
• N/A
Should not have
• No cars or standard trucks, please refer to the attached images to understand the product . Should not have any new logos or branding. No other colours besides what is in the logo you choose.

```html
<!DOCTYPE html>
<html lang="en">
<head>
<meta charset="utf-8">
<title>Coastal Iron Haulers Motor Co – Business Card</title>
<link rel="stylesheet" href="https://fonts.googleapis.com/css2?family=Open+Sans:wght@400;600;700&family=Michroma&display=swap">
<style>
  :root {
    --bg: #2b2b2d;
    --card-top: #1c1c1d;
    --card-bottom: #070707;
    --red: #e0141e;
    --red-dark: #7a1a22;
    --white: #e9e9e9;
    --grey: #b9b9b9;
    --rule: #3a3a3c;
    --vehicle-light: #2a2a2c;
    --vehicle-dark: #111112;
  }
  * { box-sizing: border-box; margin: 0; padding: 0; }
  html, body {
    width: 1200px; height: 900px; overflow: hidden;
    background: var(--bg);
    font-family: "Open Sans", Arial, sans-serif;
  }
  .stage {
    width: 1200px; height: 900px;
    display: flex; flex-direction: column;
    align-items: center; justify-content: center; gap: 40px;
  }
  .card {
    position: relative;
    width: 580px; height: 340px;
    background: linear-gradient(160deg, var(--card-top), var(--card-bottom));
    overflow: hidden;
    display: flex; flex-direction: column;
    align-items: center; justify-content: center;
    text-align: center;
  }
  .card__stripe {
    position: absolute; left: 0; right: 0; bottom: 0; height: 12px;
    background: linear-gradient(90deg, var(--red-dark), var(--red));
  }
  /* Front */
  .vehicle {
    width: 260px; height: 80px;
    margin-bottom: 22px;
    border-radius: 4px;
    background: radial-gradient(ellipse at 50% 60%, var(--vehicle-light), var(--vehicle-dark) 75%);
  }
  .brand {
    display: flex; align-items: center; gap: 12px;
    color: var(--white);
    font-weight: 700; font-size: 25px; letter-spacing: 0.5px;
    white-space: nowrap;
  }
  .brand__mark { width: 12px; height: 12px; background: var(--red); }
  .card__web {
    margin-top: 30px;
    color: var(--red);
    font-size: 17px; letter-spacing: 2.5px;
  }
  /* Back */
  .card--back { padding-bottom: 12px; }
  .contact { width: 320px; }
  .contact__name {
    font-family: "Michroma", "Open Sans", sans-serif;
    font-weight: 400;
    color: var(--red);
    font-size: 17px; letter-spacing: 2px; text-transform: uppercase;
    white-space: nowrap;
  }
  .contact__role { color: var(--grey); font-size: 14px; margin-top: 1px; }
  .contact__rule { height: 1px; background: var(--rule); margin: 7px 0; }
  .contact__line { color: var(--grey); font-size: 14px; line-height: 1.4; white-space: nowrap; }
  .contact__label { color: var(--red); font-weight: 600; }
  .contact__address .contact__line { font-size: 15px; }
  .contact__licence { margin-top: 4px; font-size: 13px; }
</style>
</head>
<body>
  <main class="stage">
    <section class="card card--front">
      <div class="vehicle" role="img" aria-label="Photo of a black KRV Sorrento pick-up truck, front view"></div>
      <div class="brand">
        <span class="brand__mark"></span>
        <span class="brand__name">Coastal Iron Haulers Motor Co</span>
      </div>
      <p class="card__web">qelvtrk.com.au</p>
      <div class="card__stripe"></div>
    </section>

    <section class="card card--back">
      <div class="contact">
        <h1 class="contact__name">Dennis Harlowe</h1>
        <p class="contact__role">Managing Director</p>
        <div class="contact__rule"></div>
        <p class="contact__line"><span class="contact__label">P:</span> 0412 639 274</p>
        <p class="contact__line"><span class="contact__label">E:</span> den@qelvtrk.com.au</p>
        <p class="contact__line"><span class="contact__label">W:</span> qelvtrk.com.au</p>
        <div class="contact__rule"></div>
        <div class="contact__address">
          <p class="contact__line">Level 5, Brindle Parkway</p>
          <p class="contact__line">17 Pemberly Lane</p>
          <p class="contact__line">Baulkham Hills NSW, Australia</p>
        </div>
        <p class="contact__line contact__licence"><span class="contact__label">Licence No:</span> MD493152</p>
      </div>
      <div class="card__stripe"></div>
    </section>
  </main>
</body>
</html>
```